Harvest Gateway Fellowship Ministries needs a fresh new web design

We are an up and coming multicultural church that aims to bring people into a life changing encounter with God. We need a fresh and inviting website in order to increase our internet presence and make us easier to connect with.
Here are some of the basic requirements for the site:
• Clearly displayed address, service times, and contact info
• A staff profile page
• An area for a calendar with upcoming events and their details
• Social media buttons
• Group pages for the different ministries (youth, children’s church, men, etc…)
• An area for donations and eCommerce
• A resources page for assorted media (podcasts, sermons, videos, etc.…)
• An area for prayer requests.

```html
<!DOCTYPE html>
<html lang="en">
<head>
<meta charset="utf-8">
<title>Harvest Gateway Fellowship Ministries – Contact</title>
<link href="https://fonts.googleapis.com/css2?family=Lato:wght@400;700&display=swap" rel="stylesheet">
<style>
:root{
  --royal:#1c0f95;
  --gold:#e8c30d;
  --gold-text:#d9a800;
  --nav-text:#4a3a00;
  --nav-rule:#c9a300;
  --ink:#333;
  --muted:#555;
  --page:#f2f2f2;
  --line:#d5d5d5;
  --soft-grey:#9a9a9a;
  --footer-text:#c9c6ef;
}
*{box-sizing:border-box;margin:0;padding:0}
html,body{width:993px;height:1200px;overflow:hidden}
body{font-family:'Lato',sans-serif;color:var(--ink);background:var(--page);position:relative}

.topbar{height:33px;background:var(--royal);color:#fff;font-size:12px;display:flex;align-items:center;padding:0 82px;white-space:nowrap}
.topbar .tagline{flex:1}
.topbar .schedule-title{margin-right:8px}
.topbar .times{border-left:2px solid #fff;padding-left:8px;font-size:10px;line-height:11px}

.header{height:95px;background:#fff;position:relative;overflow:hidden}
.brand{position:absolute;left:84px;top:18px;display:flex;align-items:center;gap:8px}
.brand .mark{width:34px;height:34px;border-radius:50%;background:var(--gold);flex:none}
.brand .name{font-size:16px;font-weight:700;color:var(--royal);line-height:18px;white-space:nowrap}
.info{position:absolute;top:20px;text-align:right;font-size:12px;color:var(--muted);line-height:13px;white-space:nowrap}
.info h3{font-size:14px;font-weight:700;color:#444;margin-bottom:3px;line-height:16px}
.info a{color:var(--gold-text);font-size:10px;text-decoration:none}
.info.donate{right:520px}
.info.prayer{right:287px}
.info.address{right:139px}
.divider{position:absolute;top:24px;width:1px;height:50px;background:var(--line)}
.social{position:absolute;left:888px;top:24px;display:flex;flex-direction:column;gap:3px}
.social span{width:22px;height:22px;border-radius:50%;background:var(--soft-grey);display:block}

.nav{height:34px;background:var(--gold);position:relative;font-size:12px;white-space:nowrap}
.nav a{position:absolute;top:10px;color:var(--nav-text);text-decoration:none;line-height:14px}
.nav .sep{position:absolute;top:11px;width:1px;height:12px;background:var(--nav-rule)}

.hero{height:83px;background:linear-gradient(90deg,#3a2a0c,#6a4d14 40%,#3d2c0a 70%,#5a4312);padding:22px 82px;color:#fff}
.hero .crumbs{font-size:11px}
.hero h1{font-size:21px;font-weight:700;margin-top:2px}

.content{position:absolute;top:245px;left:0;width:993px;height:498px}
.intro{position:absolute;left:90px;top:45px;width:525px;font-size:12px;line-height:18px;color:var(--muted)}
.field{position:absolute}
.field label{display:block;font-size:12px;color:#333;margin-bottom:6px}
.field .box{background:#fff;border:1px solid #e0e0e0;border-radius:3px;height:33px}
.send{position:absolute;left:91px;top:407px;width:199px;height:41px;background:var(--gold);color:#fff;font-size:13px;display:flex;align-items:center;justify-content:center;border-radius:2px}
.side{position:absolute;left:653px;top:46px;font-size:11px;line-height:16.5px;color:var(--muted)}
.side h2{font-size:15px;font-weight:400;color:#333;margin-bottom:4px}

.map{position:absolute;top:743px;left:0;width:993px;height:207px;background:linear-gradient(90deg,#ecebe4,#efeee8 50%,#e8e6df);border-top:1px solid #ccc}

.footer{position:absolute;top:950px;left:0;width:993px;height:250px;background:var(--royal);color:var(--footer-text)}
.col{position:absolute;top:35px;font-size:11px;line-height:15px}
.col h4{font-size:15px;font-weight:400;color:#fff;margin-bottom:12px;text-transform:uppercase;white-space:nowrap}
.col ul{list-style:none;line-height:20px;white-space:nowrap}
.contact-line{display:flex;align-items:center;gap:8px;margin-top:2px;font-size:12px;white-space:nowrap}
.email-input{width:188px;height:27px;background:#eee;border-radius:2px;color:#aaa;font-size:11px;padding:7px 10px;margin-top:6px}
.subscribe{width:77px;height:27px;background:var(--gold);color:#2a2000;font-size:11px;border-radius:2px;display:flex;align-items:center;justify-content:center;margin-top:9px}
.footer-social{display:flex;gap:7px;margin-top:8px}
.footer-social span{width:26px;height:26px;border-radius:50%;background:#8e88c8;display:block}
.copyright{position:absolute;left:82px;right:82px;top:186px;border-top:1px solid #3a2fa8;text-align:center;font-size:10px;padding-top:14px;letter-spacing:.3px}
</style>
</head>
<body>
<div class="topbar">
  <div class="tagline">A house of prayer for all nations, where the love, the presence and the power of God are real.</div>
  <div class="schedule-title">SUNDAY SERVICE SCHEDULE</div>
  <div class="times">09:00 A.M. | Sunday School<br>10:30 A.M. | Convergent Service</div>
</div>

<header class="header">
  <div class="brand"><span class="mark"></span><span class="name">Harvest Gateway<br>Fellowship Ministries</span></div>
  <div class="info donate"><h3>Donate</h3>Lorem Ipsum is simply<br>dummy text of the printing<br><a href="#">Donate Now »</a></div>
  <div class="divider" style="left:490px"></div>
  <div class="info prayer"><h3>Request Prayer</h3>Lorem Ipsum is simply dummy text<br>of the printing and typesetting industry.<br><a href="#">Request Now »</a></div>
  <div class="divider" style="left:723px"></div>
  <div class="info address"><h3>Address</h3>Harvest Gateway<br>City, Location<br><a href="#">Contact »</a></div>
  <div class="divider" style="left:870px"></div>
  <div class="social"><span></span><span></span></div>
</header>

<nav class="nav">
  <a href="#" style="left:96px">Home</a><span class="sep" style="left:146px"></span>
  <a href="#" style="left:169px">About</a><span class="sep" style="left:220px"></span>
  <a href="#" style="left:243px">Staff Profile</a><span class="sep" style="left:321px"></span>
  <a href="#" style="left:346px">News and Events</a><span class="sep" style="left:452px"></span>
  <a href="#" style="left:475px">Worship &amp; Services</a><span class="sep" style="left:593px"></span>
  <a href="#" style="left:613px">Groups</a><span class="sep" style="left:671px"></span>
  <a href="#" style="left:693px">Shop</a><span class="sep" style="left:740px"></span>
  <a href="#" style="left:761px">Resources</a><span class="sep" style="left:834px"></span>
  <a href="#" style="left:856px">Contact</a>
</nav>

<section class="hero" role="img" aria-label="Banner photo of a golden wheat field">
  <div class="crumbs">Home &gt; Contact</div>
  <h1>Contact</h1>
</section>

<main class="content">
  <p class="intro">Lorem Ipsum is simply dummy text of the printing and typesetting industry. Lorem Ipsum has been the industry's standard dummy text.</p>
  <div class="field" style="left:91px;top:98px;width:253px"><label>First Name</label><div class="box"></div></div>
  <div class="field" style="left:360px;top:98px;width:253px"><label>Last Name</label><div class="box"></div></div>
  <div class="field" style="left:91px;top:164px;width:253px"><label>Email</label><div class="box"></div></div>
  <div class="field" style="left:360px;top:164px;width:253px"><label>Ph</label><div class="box"></div></div>
  <div class="field" style="left:91px;top:230px;width:522px"><label>Comments</label><div class="box" style="height:141px"></div></div>
  <div class="send">SEND</div>
  <aside class="side">
    <h2>Address</h2>
    Harvest Gateway Fellowship Ministries<br>Building Name, Street Numbrt,<br>City, State<br><br>Ph: 123456789<br>Email: info@harvestgatewayfm.org
  </aside>
</main>

<div class="map" role="img" aria-label="Road map showing the church location with a location pin"></div>

<footer class="footer">
  <div class="col" style="left:82px">
    <h4>Contact Us</h4>
    Harvest Gateway<br>Location, city<br>State Name, Country
    <div class="contact-line" style="margin-top:10px">
      <svg width="13" height="13" viewBox="0 0 24 24"><path fill="#c9c6ef" d="M6.6 10.8c1.4 2.8 3.8 5.1 6.6 6.6l2.2-2.2c.3-.3.7-.4 1-.2 1.1.4 2.3.6 3.6.6.6 0 1 .4 1 1V20c0 .6-.4 1-1 1C10.6 21 3 13.4 3 4c0-.6.4-1 1-1h3.5c.6 0 1 .4 1 1 0 1.3.2 2.5.6 3.6.1.3 0 .7-.2 1z"/></svg>
      +1 555-204-7310
    </div>
    <div class="contact-line">
      <svg width="13" height="10" viewBox="0 0 13 10"><rect width="13" height="10" fill="#c9c6ef"/><path d="M0 0l6.5 5L13 0" stroke="#1c0f95" fill="none"/></svg>
      hello@harvestgatewayfm.org
    </div>
  </div>
  <div class="col" style="left:266px">
    <h4>Communities We Serve</h4>
    <div style="display:flex;gap:22px">
      <ul><li>• Lorem Ipsum</li><li>• Dummy Links</li><li>• More dummy</li><li>• Sample Text</li><li>• More samples</li></ul>
      <ul><li>• type text dummy</li><li>• Lorem Ipsum</li></ul>
    </div>
  </div>
  <div class="col" style="left:496px">
    <h4>Newsletter</h4>
    Enter your email below to get notified
    <div class="email-input">Your Email</div>
    <div class="subscribe">Subscribe</div>
  </div>
  <div class="col" style="left:726px;width:190px">
    <h4>Connect With Us</h4>
    Stay connected for the latest updates at Harvest Gateway Fellowship
    <div class="footer-social"><span></span><span></span></div>
  </div>
  <div class="copyright">Copyright © 2014. All rights reserved. Harvest Gateway.</div>
</footer>
</body>
</html>
```